Packaging design for a reclosable bag for our product

We have a logo, and we need to put it on packaging for our product and while we want the look to be simple, we want it to follow good design principles and also contain spaces for other product descriptions.

There will be 5 sizes at launch so I'd like 5 variations, one for each size.

I've included a few mockups of the type of bag that I made but they are all just rough ideas that I had.

I want the brand to look scientific and methodical and even a bit quirky, as in "wow this is a serious product but also a bit unusual."

```html
<!DOCTYPE html>
<html lang="en">
<head>
<meta charset="utf-8">
<title>Kelvo Bias Lighting – pouch packaging</title>
<link rel="stylesheet" href="https://fonts.googleapis.com/css2?family=Josefin+Sans:wght@400;700&display=swap">
<style>
  :root {
    --canvas: #ffffff;
    --pouch: #1b1b1b;
    --pouch-band: #2a2a2a;
    --pouch-seal: #121212;
    --ink: #ffffff;
    --size-xl: #1787d8;
    --size-l: #e0141b;
  }
  * { box-sizing: border-box; margin: 0; padding: 0; }
  html, body { width: 1200px; height: 1200px; overflow: hidden; background: var(--canvas); }
  body { position: relative; font-family: "Josefin Sans", sans-serif; color: var(--ink); }

  .pouch {
    position: absolute;
    background: var(--pouch);
    border-radius: 22px 22px 4px 4px;
    overflow: hidden;
  }
  .pouch--xl { left: 194px; top: 242px; width: 492px; height: 730px; z-index: 1; }
  .pouch--l  { left: 614px; top: 354px; width: 448px; height: 666px; z-index: 2; }

  .pouch__side-band { position: absolute; left: 0; top: 0; bottom: 0; background: var(--pouch-band); }
  .pouch--xl .pouch__side-band { width: 78px; }
  .pouch--l  .pouch__side-band { width: 74px; }

  .pouch__seal { position: absolute; left: 0; right: 0; height: 4px; background: var(--pouch-seal); }
  .pouch--xl .pouch__seal { top: 84px; }
  .pouch--l  .pouch__seal { top: 78px; }
  .pouch__seal--lower { opacity: .7; }
  .pouch--xl .pouch__seal--lower { top: 104px; }
  .pouch--l  .pouch__seal--lower { top: 96px; }

  .size-tab__strip { position: absolute; left: 0; background: #141414; }
  .pouch--xl .size-tab__strip { top: 424px; width: 90px; height: 96px; }
  .pouch--l  .size-tab__strip { top: 376px; width: 84px; height: 90px; }

  .size-tab {
    position: absolute;
    display: flex; align-items: center; justify-content: center;
    font-weight: 700; color: var(--ink);
  }
  .size-tab span { transform: rotate(-90deg); display: block; }
  .pouch--xl .size-tab { left: 13px; top: 436px; width: 77px; height: 72px; background: var(--size-xl); font-size: 34px; }
  .pouch--l  .size-tab { left: 10px; top: 388px; width: 70px; height: 66px; background: var(--size-l); font-size: 30px; }

  .length {
    position: absolute;
    white-space: nowrap;
    transform: rotate(-90deg);
    transform-origin: left top;
    font-size: 30px;
  }
  .length b { font-weight: 700; font-size: 40px; }
  .pouch--xl .length { left: 24px; top: 402px; color: var(--size-xl); }
  .pouch--l  .length { left: 28px; top: 360px; color: var(--size-l); font-size: 28px; }

  .brand { position: absolute; font-weight: 700; line-height: 1; letter-spacing: -1px; }
  .product { position: absolute; font-weight: 400; line-height: 1; }
  .variant { position: absolute; font-weight: 400; line-height: 1; }
  .specs { position: absolute; font-weight: 400; line-height: 1.3; letter-spacing: .4px; }

  .pouch--xl .brand   { left: 115px; top: 262px; font-size: 56px; }
  .pouch--xl .product { left: 115px; top: 346px; font-size: 31px; }
  .pouch--xl .variant { left: 115px; top: 384px; font-size: 19px; }
  .pouch--xl .specs   { left: 116px; top: 444px; font-size: 21px; }

  .pouch--l .brand   { left: 104px; top: 230px; font-size: 52px; }
  .pouch--l .product { left: 104px; top: 302px; font-size: 30px; }
  .pouch--l .variant { left: 104px; top: 338px; font-size: 18px; }
  .pouch--l .specs   { left: 104px; top: 398px; font-size: 20px; }
</style>
</head>
<body>
  <section class="pouch pouch--xl" aria-label="Extra large pouch">
    <div class="pouch__side-band"></div>
    <div class="pouch__seal"></div>
    <div class="pouch__seal pouch__seal--lower"></div>
    <div class="length"><b>5</b> meters</div>
    <div class="size-tab__strip"></div>
    <div class="size-tab"><span>XL</span></div>
    <div class="brand">Kelvo</div>
    <div class="product">Bias Lighting</div>
    <div class="variant">Extra large</div>
    <p class="specs">Simulated D65 CRI 90+<br>6500K White Bias Lighting</p>
  </section>

  <section class="pouch pouch--l" aria-label="Large pouch">
    <div class="pouch__side-band"></div>
    <div class="pouch__seal"></div>
    <div class="pouch__seal pouch__seal--lower"></div>
    <div class="length"><b>4</b> meters</div>
    <div class="size-tab__strip"></div>
    <div class="size-tab"><span>L</span></div>
    <div class="brand">Kelvo</div>
    <div class="product">Bias Lighting</div>
    <div class="variant">Extra large</div>
    <p class="specs">Simulated D65 CRI 90+<br>6500K White Bias Lighting</p>
  </section>
</body>
</html>
```